Business card por a urban DJ, up scale audience target

Need a sober design, modern, conservative colors but i can consider some options, y play rnb, hip hop, EDM and top40.

Business card for contact and personal info, double sided, use logo attrached please; im 42 so i need a card acording to my age an target audience.

Target Market(s)

Adult people, up scale audience

Industry/Entity Type

Music Download

Contact Information for Business Card

Cel (318) 4207265518 www.lumadrift.com

Requirements
Must have
• open mind
Nice to have
• open mind
Should not have
• DJ

```html
<!DOCTYPE html>
<html lang="en">
<head>
<meta charset="utf-8">
<title>Lumadrift Business Card</title>
<link href="https://fonts.googleapis.com/css2?family=Arimo:wght@400;700&family=Libre+Franklin:wght@600&display=swap" rel="stylesheet">
<style>
  :root {
    --stage: #e4e4e4;
    --ink: #000000;
    --logo-ink: #2b2b2b;
    --paper: #ffffff;
    --band: #a3a3a3;
    --text-light: #ffffff;
  }
  * { margin: 0; padding: 0; box-sizing: border-box; }
  html, body { width: 992px; height: 1200px; overflow: hidden; }
  body { background: var(--stage); position: relative; font-family: "Arimo", Arial, sans-serif; }

  .card {
    position: absolute;
    left: 97px;
    width: 801px;
    height: 458px;
    overflow: hidden;
    box-shadow: 4px 6px 10px rgba(0,0,0,0.35);
  }
  .card--front { top: 102px; background: var(--ink); }
  .card--back { top: 619px; background: var(--ink); }

  .front-top {
    position: absolute; left: 0; top: 0; width: 100%; height: 246px;
    background: var(--paper);
    display: flex; align-items: center; justify-content: center;
  }
  .front-band {
    position: absolute; left: 0; top: 246px; width: 100%; height: 19px;
    background: var(--band);
  }

  .brand {
    font-family: "Libre Franklin", Arial, sans-serif;
    font-weight: 600;
    font-size: 62px;
    letter-spacing: 4px;
    line-height: 1;
    display: flex; align-items: center; gap: 18px;
  }
  .brand__mark { width: 30px; height: 30px; }
  .brand--dark { color: var(--logo-ink); padding-top: 20px; }
  .brand--dark .brand__mark { background: var(--logo-ink); }
  .brand--light { color: var(--text-light); }
  .brand--light .brand__mark { background: var(--text-light); }

  .card--back .back-center {
    position: absolute; inset: 0;
    display: flex; align-items: center; justify-content: center;
    padding-top: 20px;
  }

  .identity { position: absolute; left: 26px; top: 295px; color: var(--text-light); }
  .identity__name {
    font-family: "Libre Franklin", Arial, sans-serif;
    font-weight: 600; font-size: 29px; line-height: 1.1;
  }
  .identity__role { font-size: 21px; margin-top: 8px; }

  .divider {
    position: absolute; left: 313px; top: 298px;
    width: 3px; height: 138px; background: var(--text-light);
  }

  .contacts {
    position: absolute; left: 345px; top: 302px;
    list-style: none; color: var(--text-light);
  }
  .contacts li {
    display: flex; align-items: center; gap: 17px;
    font-size: 19.5px; height: 35.5px; letter-spacing: 0.3px;
  }
  .contacts svg { width: 15px; height: 15px; flex: none; }
</style>
</head>
<body>

<section class="card card--front">
  <div class="front-top">
    <div class="brand brand--dark"><span class="brand__mark"></span>LUMADRIFT</div>
  </div>
  <div class="front-band"></div>

  <div class="identity">
    <p class="identity__name">Marcus Ellwood</p>
    <p class="identity__role">Managing Director</p>
  </div>

  <div class="divider"></div>

  <ul class="contacts">
    <li>
      <svg viewBox="0 0 16 16" aria-hidden="true"><rect width="16" height="16" rx="2" fill="#fff"/><path d="M3 6c0-2 2-3 5-3s5 1 5 3l-2 1-1-1.5H6L5 7z M4 12l1-4h6l1 4z" fill="#000"/></svg>
      (318) 4207265518
    </li>
    <li>
      <svg viewBox="0 0 16 16" aria-hidden="true"><rect width="16" height="16" rx="2" fill="#fff"/><circle cx="8" cy="8" r="5.5" fill="#000"/><path d="M5 5.5c1.5 0 2 1 1.5 2s1 1.5 1 3M9.5 4c0 1.5 1.5 1.5 2.5 2.5" stroke="#fff" stroke-width="1" fill="none"/></svg>
      www.lumadrift.com
    </li>
    <li>
      <svg viewBox="0 0 16 16" aria-hidden="true"><rect width="16" height="16" rx="2" fill="#fff"/><rect x="3" y="4.5" width="10" height="7" fill="#000"/><path d="M3 4.5l5 4 5-4" stroke="#fff" stroke-width="1" fill="none"/></svg>
      info@lumadrift,com
    </li>
    <li>
      <svg viewBox="0 0 16 16" aria-hidden="true"><rect width="16" height="16" rx="2" fill="#fff"/><path d="M8 13s-4-4.2-4-7a4 4 0 0 1 8 0c0 2.8-4 7-4 7z" fill="#000"/><circle cx="8" cy="6" r="1.5" fill="#fff"/></svg>
      84 Harlow St, Suite Brookline MA 0246
    </li>
  </ul>
</section>

<section class="card card--back">
  <div class="back-center">
    <div class="brand brand--light"><span class="brand__mark"></span>LUMADRIFT</div>
  </div>
</section>

</body>
</html>
```